Cocktail-Making Assistant App re-design

Ok boys and girls, here's the deal:
I have an android app which is almost complete, but needs a design overhaul.

The app is a standard cocktail-making assistant: gives you a list of cocktails and the ability to see which cocktail you can make out of those ingredients (drinks, fruit, etc) you have at home.

I've attached some general app flow, as well as detailed requirements/explanation presentation. Most of those things are just FYI, so that you know what it's about.

3 screens are the most important (main screen, cocktail view screen, ingredient view screen), meaning I will pick the design mostly based on ideas for those 3 things, with the fourth being a rather simple list (given on attached flow, third tier)
Some other screens are derived from that, with some minor changes on it, but you shouldn't care about that.

There are lots of other, non-explained things which I said nothing about only because they are (from design point of view) completely the same and would only make it seem more complicated.

I don't want to influence the colour scheme, but the app will be released under RedFig developer name (having a light colured red fig as a logo) so I suppose some brownish design, for example, will not really fit nicely. If you, however, have a killer which you are confident will prove me wrong, I'm looking forward to seeing it!

It should be a serious, elegant look (as opposed to cartoonish, but we are not aiming for a business look at all!), not cluttered with details, no clubbing themes, glitter and so on.

Test apk file available on request (Android 2.3+).

Edit: payment is now guaranteed
Also please note that currently, the favorite, "heart" button has a motion effect:
on click it flies out of the screen to the left (white heart) and comes back to the screen as a red heart. Take that into consideration, if it means anything to you.

Target Market(s)

Whoever you imagine would enjoy drinking cocktails

Industry/Entity Type

Business

Requirements
Must have
• Everything is said in the provided documentation - images say more than I could possibly write here.
Nice to have
• As said, most of the icons are a nice-to-have. Only those which are critically linked to the rest of the design must be provided. More details in the docs.
Should not have
• No cartoon look, No zillion colours

```html
<!DOCTYPE html>
<html lang="en">
<head>
<meta charset="utf-8">
<title>Cocktail App – Main Screen</title>
<link href="https://fonts.googleapis.com/css2?family=Questrial&display=swap" rel="stylesheet">
<style>
  :root {
    --stage: #58595b;
    --screen: #f1f1f1;
    --screen-glow: #fbfbfb;
    --header-top: #62b8de;
    --header-bottom: #b3dcef;
    --white: #ffffff;
    --ink: #555555;
    --icon: #6d6d6d;
    --rule: #bfbfbf;
    --tile-shaker: #e3cfa6;
    --tile-bar: #9de5cd;
    --tile-cocktails: #d6f5d7;
    --tile-favorites: #e3b8a6;
    --tile-shopping: #cee3f3;
    --tile-featured: #d8cdd2;
  }
  * { box-sizing: border-box; margin: 0; padding: 0; }
  html, body {
    width: 939px; height: 1200px; overflow: hidden;
    background: var(--stage);
    font-family: "Questrial", sans-serif;
  }
  .screen {
    position: absolute; left: 79px; top: 23px;
    width: 767px; height: 1112px;
    background: radial-gradient(ellipse at 50% 55%, var(--screen-glow) 0%, var(--screen) 70%);
  }
  .app-header {
    position: absolute; left: 0; top: 0; width: 100%; height: 122px;
    background: linear-gradient(to bottom, var(--header-top), var(--header-bottom));
  }
  .back-button {
    position: absolute; left: 26px; top: 27px; width: 70px; height: 70px;
  }
  .app-title {
    position: absolute; left: 0; right: 0; top: 30px;
    text-align: center; color: var(--white);
    font-size: 49px; font-weight: 400; letter-spacing: 0.5px;
  }
  .menu-grid { position: absolute; left: 16px; top: 205px; }
  .tile {
    position: absolute; width: 359px; height: 221px;
  }
  .tile svg { position: absolute; left: 0; top: 0; width: 359px; height: 221px; }
  .tile-label {
    position: absolute; left: 0; right: 0; bottom: 12px;
    text-align: center; color: var(--ink); font-size: 27px;
  }
  .tile--shaker { left: 0; top: 0; background: var(--tile-shaker); }
  .tile--bar { left: 371px; top: 0; background: var(--tile-bar); }
  .tile--cocktails { left: 0; top: 235px; background: var(--tile-cocktails); }
  .tile--favorites { left: 371px; top: 235px; background: var(--tile-favorites); }
  .tile--shopping { left: 0; top: 468px; background: var(--tile-shopping); }
  .tile--featured { left: 371px; top: 468px; background: var(--tile-featured); }
  .status-bar {
    position: absolute; left: 13px; top: 951px; width: 738px; height: 104px;
    border-top: 5px solid var(--rule); border-bottom: 5px solid var(--rule);
  }
  .points {
    position: absolute; left: 16px; top: 29px;
    font-size: 33px; color: var(--ink);
  }
  .settings-button {
    position: absolute; right: 6px; top: 9px; width: 82px; height: 82px;
  }
</style>
</head>
<body>
<main class="screen">
  <header class="app-header">
    <svg class="back-button" viewBox="0 0 70 70" aria-label="Back">
      <circle cx="35" cy="35" r="32" fill="none" stroke="#fff" stroke-width="4"/>
      <circle cx="35" cy="35" r="20" fill="#fff"/>
      <path d="M45 35H27M35 26l-9 9 9 9" fill="none" stroke="#8cc9e6" stroke-width="5" stroke-linecap="round" stroke-linejoin="round"/>
    </svg>
    <h1 class="app-title">Cocktail App</h1>
  </header>

  <nav class="menu-grid">
    <a class="tile tile--shaker">
      <svg viewBox="0 0 359 221" fill="none" stroke="var(--icon)" stroke-width="5" stroke-linejoin="round">
        <path d="M167 55c0-14 25-14 25 0"/>
        <rect x="160" y="55" width="39" height="14" rx="3"/>
        <path d="M156 69h47l-5 30h-37z"/>
        <path d="M161 99h37l-5 61h-27z"/>
        <path d="M179 80v16"/>
      </svg>
      <span class="tile-label">Shaker</span>
    </a>
    <a class="tile tile--bar">
      <svg viewBox="0 0 359 221" fill="none" stroke="var(--icon)" stroke-width="5" stroke-linejoin="round">
        <path d="M116 54h10v18l9 20v66h-28V92l9-20z"/>
        <path d="M150 54h10v18l9 20v66h-28V92l9-20z"/>
        <path d="M187 90h32c4 20-2 36-16 38-14-2-20-18-16-38z"/>
        <path d="M190 107h26"/>
        <path d="M203 128v28M190 157h26"/>
      </svg>
      <span class="tile-label">My Bar</span>
    </a>
    <a class="tile tile--cocktails">
      <svg viewBox="0 0 359 221" fill="none" stroke="var(--icon)" stroke-width="5" stroke-linejoin="round" stroke-linecap="round">
        <path d="M145 76h68l-34 40z"/>
        <path d="M179 116v38M162 156h34"/>
        <path d="M162 95l54-39"/>
        <path d="M214 50c6-7 10-4 8 4l-4 9z" fill="var(--icon)"/>
      </svg>
      <span class="tile-label">Cocktails</span>
    </a>
    <a class="tile tile--favorites">
      <svg viewBox="0 0 359 221" fill="none" stroke="var(--icon)" stroke-width="6" stroke-linejoin="round">
        <path d="M179 153l-38-42c-16-19-3-45 18-42 10 1 17 8 20 15 3-7 10-14 20-15 21-3 34 23 18 42z"/>
      </svg>
      <span class="tile-label">Favorites</span>
    </a>
    <a class="tile tile--shopping">
      <svg viewBox="0 0 359 221" fill="none" stroke="var(--icon)" stroke-width="5" stroke-linejoin="round" stroke-linecap="round">
        <path d="M103 75h24l18 56h55l18-48H132"/>
        <path d="M143 99h71M150 115h58"/>
        <circle cx="156" cy="149" r="8" fill="var(--icon)"/>
        <circle cx="191" cy="149" r="8" fill="var(--icon)"/>
      </svg>
      <span class="tile-label">Shopping List</span>
    </a>
    <a class="tile tile--featured">
      <svg viewBox="0 0 359 221" fill="var(--icon)">
        <path d="M160 90l-12 54 12-6 8 10 11-46zM198 90l12 54-12-6-8 10-11-46z"/>
        <circle cx="179" cy="72" r="22" fill="var(--icon)"/>
        <circle cx="179" cy="72" r="15" fill="#cdbfc6"/>
        <path d="M179 62l3 7h7l-6 5 2 7-6-4-6 4 2-7-6-5h7z"/>
      </svg>
      <span class="tile-label">Featured</span>
    </a>
  </nav>

  <footer class="status-bar">
    <span class="points">Points - 100</span>
    <svg class="settings-button" viewBox="0 0 82 82" aria-label="Settings">
      <circle cx="41" cy="41" r="37" fill="none" stroke="#555" stroke-width="5"/>
      <g fill="#555" transform="translate(41 41)">
        <circle r="17"/>
        <rect x="-5" y="-25" width="10" height="50" rx="2"/>
        <rect x="-5" y="-25" width="10" height="50" rx="2" transform="rotate(45)"/>
        <rect x="-5" y="-25" width="10" height="50" rx="2" transform="rotate(90)"/>
        <rect x="-5" y="-25" width="10" height="50" rx="2" transform="rotate(135)"/>
        <circle r="7" fill="#f1f1f1"/>
      </g>
    </svg>
  </footer>
</main>
</body>
</html>
```